RW Framewell Inc Business cards

We need business cards using our existing logo but slightly modified. Right now the logo says RW Loadbearing Masonry. We want to keep the RW part of the design, but replace the Structural Concrete portion with "FRAMEWELL". Please see the attached file.
Ideally this would be a blank template so we can add Different Names, titles, and phone numbers later.
On the one side we want only the logo and on the other side the detail. I'm attaching an example for you to see.
Please reach out with any other questions. Our address and other details will be given out once we find a design we like.

Target Market(s)

Construction Industry

```html
<!DOCTYPE html>
<html lang="en">
<head>
<meta charset="utf-8">
<title>RW Framewell Inc – Business Cards</title>
<link rel="stylesheet" href="https://fonts.googleapis.com/css2?family=Michroma&family=Open+Sans:wght@400;600&display=swap">
<style>
  :root {
    --stage: #1e1e1e;
    --brand-blue: #1173c0;
    --brand-blue-deep: #0f68b0;
    --ink-grey: #6f6f6f;
    --paper: #ffffff;
    --white: #ffffff;
  }
  * { box-sizing: border-box; margin: 0; padding: 0; }
  html, body {
    width: 1200px; height: 900px; overflow: hidden;
    background: var(--stage);
  }
  .stage {
    position: relative; width: 1200px; height: 900px;
  }
  .card {
    position: absolute; left: 250px; width: 700px; height: 400px;
    box-shadow: 0 12px 30px rgba(0,0,0,0.55);
  }
  /* Logo side */
  .card--back {
    top: 40px;
    background: linear-gradient(160deg, var(--brand-blue) 0%, var(--brand-blue-deep) 100%);
    display: flex; align-items: center; justify-content: center;
  }
  .wordmark {
    font-family: 'Michroma', sans-serif;
    font-weight: 400;
    letter-spacing: 2px;
    white-space: nowrap;
  }
  .card--back .wordmark {
    color: var(--white); font-size: 46px;
  }
  /* Detail side */
  .card--front {
    top: 460px; background: var(--paper);
  }
  .card--front .wordmark {
    position: absolute; left: 46px; top: 38px;
    color: var(--brand-blue); font-size: 34px;
  }
  .person {
    position: absolute; left: 46px; top: 150px;
  }
  .person__name {
    font-family: 'Michroma', sans-serif;
    color: var(--brand-blue); font-size: 27px; letter-spacing: 1px;
    white-space: nowrap;
  }
  .person__title {
    font-family: 'Open Sans', sans-serif;
    color: var(--ink-grey); font-size: 19px; margin-top: 2px;
  }
  .divider {
    position: absolute; left: 46px; right: 46px; top: 238px;
    height: 2px; background: var(--brand-blue);
  }
  .contacts {
    position: absolute; left: 46px; top: 254px; list-style: none;
    font-family: 'Open Sans', sans-serif; color: var(--ink-grey); font-size: 19px;
  }
  .contacts li {
    display: flex; align-items: center; gap: 12px; height: 29px;
  }
  .contacts svg { width: 18px; height: 18px; fill: var(--brand-blue); flex: none; }
  .address {
    position: absolute; right: 46px; bottom: 30px; text-align: right;
    font-family: 'Open Sans', sans-serif; font-style: normal;
    color: var(--ink-grey); font-size: 19px; line-height: 1.4;
  }
</style>
</head>
<body>
<main class="stage">
  <section class="card card--back" aria-label="Logo side">
    <span class="wordmark">RW FRAMEWELL</span>
  </section>

  <section class="card card--front" aria-label="Details side">
    <span class="wordmark">RW FRAMEWELL</span>
    <div class="person">
      <p class="person__name">DORIAN KETTLEBY</p>
      <p class="person__title">Chief Officer</p>
    </div>
    <div class="divider"></div>
    <ul class="contacts">
      <li>
        <svg viewBox="0 0 24 24" aria-hidden="true"><path d="M6.6 10.8a15.1 15.1 0 0 0 6.6 6.6l2.2-2.2c.3-.3.7-.4 1-.2 1.1.4 2.3.6 3.6.6.6 0 1 .4 1 1V20c0 .6-.4 1-1 1A17 17 0 0 1 3 4c0-.6.4-1 1-1h3.5c.6 0 1 .4 1 1 0 1.3.2 2.5.6 3.6.1.3 0 .7-.2 1z"/></svg>
        <span>+00 8 38 00 00</span>
      </li>
      <li>
        <svg viewBox="0 0 24 24" aria-hidden="true"><path d="M7 1h10a2 2 0 0 1 2 2v18a2 2 0 0 1-2 2H7a2 2 0 0 1-2-2V3a2 2 0 0 1 2-2zm0 3v14h10V4zm5 15.2a1.2 1.2 0 1 0 0 2.4 1.2 1.2 0 0 0 0-2.4z"/></svg>
        <span>+00 0 90 00 00</span>
      </li>
      <li>
        <svg viewBox="0 0 24 24" aria-hidden="true"><path d="M2 5h20v14H2zm2 2v.4l8 5.3 8-5.3V7zm0 2.8V17h16V9.8l-8 5.3z"/></svg>
        <span>info@rwframewell.com</span>
      </li>
      <li>
        <svg viewBox="0 0 24 24" aria-hidden="true"><path d="M12 2a10 10 0 1 0 0 20 10 10 0 0 0 0-20zm6.9 9h-3a15 15 0 0 0-1.4-6.3A8 8 0 0 1 18.9 11zM12 4c.9 1.2 1.8 3.6 1.9 7h-3.8c.1-3.4 1-5.8 1.9-7zM9.5 4.7A15 15 0 0 0 8.1 11h-3a8 8 0 0 1 4.4-6.3zM5.1 13h3a15 15 0 0 0 1.4 6.3A8 8 0 0 1 5.1 13zM12 20c-.9-1.2-1.8-3.6-1.9-7h3.8c-.1 3.4-1 5.8-1.9 7zm2.5-.7a15 15 0 0 0 1.4-6.3h3a8 8 0 0 1-4.4 6.3z"/></svg>
        <span>www.rwframewell.com</span>
      </li>
    </ul>
    <address class="address">
      Your address line here<br>
      Country/ State
    </address>
  </section>
</main>
</body>
</html>
```